Moderne Visitenkarten für Medizintechnikfirma
Zielgruppe
Vertriebsfirma von moderner und innovativer Medizintechnik
Zielgruppe: Ärzte, Kliniken, Medizintechnikfirmen, Patienten
Aufgabenstellung
Besonderes, modernes, auffälliges und ansprechendes Design ohne überladen oder aufdringlich zu sein
Farbenorientierung kann am Logo und der Website geschehen. Wenn zum Logo harmonierend, sind aber auch andere Farben gerne gesehen.
Format: eher horizontal, vertikal aber auch möglich, abgerundete Ecken einplanen
Wenn möglich folgende Infos bitte schon auf die Karten bringen (pro Person eine Karte):
Konrad Faltermann (CEO)
konrad.faltermann@vitalis-partner.de
(Vitalis Partner GmbH
Lindenhof 12
26210 Grünstedt)
www.vitalis-partner.de
info@vitalis-partner.de
Jonas Prasken (CoS)
jonas.prasken@vitalis-partner.de
Die allgemeinen Firmeninfos können deutlich kleiner sein. Anschrift nur wenn es dadurch nicht zu viel werden würde.

```html
<!DOCTYPE html>
<html lang="de">
<head>
<meta charset="utf-8">
<title>Vitalis Partner – Visitenkarten</title>
<link rel="stylesheet" href="https://fonts.googleapis.com/css2?family=Open+Sans:wght@400;600;700&display=swap">
<style>
  :root{
    --stage:#3a3a3c;
    --card-dark:#2b2929;
    --card-light:#ffffff;
    --brand-purple:#55408f;
    --ink:#1f1f24;
    --paper-text:#f2f2f2;
  }
  *{box-sizing:border-box;margin:0;padding:0}
  html,body{width:1200px;height:978px;overflow:hidden}
  body{background:var(--stage);font-family:"Open Sans",Arial,sans-serif;position:relative}
  .card{position:absolute;left:250px;width:700px;height:424px;border-radius:18px;overflow:hidden}
  .card--back{top:40px;background:var(--card-dark)}
  .card--front{top:514px;background:var(--card-light);color:var(--ink)}

  .brand{display:flex;align-items:center;gap:18px}
  .brand__dot{width:34px;height:34px;border-radius:50%;background:var(--brand-purple);flex:none}
  .brand__name{font-weight:600;color:var(--brand-purple);letter-spacing:.5px;white-space:nowrap}

  .card--back .brand{position:absolute;left:50%;top:160px;transform:translateX(-50%)}
  .card--back .brand__name{font-size:46px}
  .card--back .brand__dot{width:44px;height:44px}
  .back__web{position:absolute;left:0;right:0;top:318px;text-align:center;color:var(--paper-text);font-size:17px;letter-spacing:.3px}

  .card--front .brand{position:absolute;left:42px;top:190px}
  .card--front .brand__name{font-size:28px}

  .divider{position:absolute;left:370px;top:64px;width:2px;height:296px;background:var(--brand-purple)}

  .contact{position:absolute;left:398px;top:62px;right:20px;font-size:14.5px;line-height:22px}
  .contact__name{font-size:23px;font-weight:700;color:var(--brand-purple);line-height:30px;margin-bottom:4px}
  .contact__row{display:flex;align-items:center;gap:10px;white-space:nowrap}
  .contact__row svg{width:15px;height:15px;flex:none;fill:var(--brand-purple)}
  .contact__block{margin-top:16px}
  .contact__address{padding-left:0}
</style>
</head>
<body>
  <section class="card card--back" aria-label="Kartenrückseite">
    <div class="brand">
      <span class="brand__dot"></span>
      <span class="brand__name">Vitalis Partner</span>
    </div>
    <p class="back__web">www.vitalis-partner.de</p>
  </section>

  <section class="card card--front" aria-label="Kartenvorderseite">
    <div class="brand">
      <span class="brand__dot"></span>
      <span class="brand__name">Vitalis Partner</span>
    </div>
    <div class="divider"></div>
    <div class="contact">
      <h1 class="contact__name">Konrad Faltermann (CEO)</h1>
      <p class="contact__row">
        <svg viewBox="0 0 24 24" aria-hidden="true"><path d="M6.6 10.8a15.1 15.1 0 0 0 6.6 6.6l2.2-2.2a1 1 0 0 1 1-.25 11.4 11.4 0 0 0 3.6.57 1 1 0 0 1 1 1V20a1 1 0 0 1-1 1A17 17 0 0 1 3 4a1 1 0 0 1 1-1h3.5a1 1 0 0 1 1 1c0 1.25.2 2.45.57 3.57a1 1 0 0 1-.25 1z"/></svg>
        +49 170 5524 3981
      </p>
      <p class="contact__row">
        <svg viewBox="0 0 24 24" aria-hidden="true"><path d="M2 5h20v14H2zm2 2v.4l8 5.2 8-5.2V7zm0 2.8V17h16V9.8l-8 5.2z"/></svg>
        konrad.faltermann@vitalis-partner.de
      </p>
      <div class="contact__block contact__address">
        <p>Vitalis Partner GmbH</p>
        <p>Lindenhof 12</p>
        <p>26210 Grünstedt</p>
      </div>
      <div class="contact__block">
        <p class="contact__row">
          <svg viewBox="0 0 24 24" aria-hidden="true"><path d="M6.6 10.8a15.1 15.1 0 0 0 6.6 6.6l2.2-2.2a1 1 0 0 1 1-.25 11.4 11.4 0 0 0 3.6.57 1 1 0 0 1 1 1V20a1 1 0 0 1-1 1A17 17 0 0 1 3 4a1 1 0 0 1 1-1h3.5a1 1 0 0 1 1 1c0 1.25.2 2.45.57 3.57a1 1 0 0 1-.25 1z"/></svg>
          0800-4419620
        </p>
        <p class="contact__row">
          <svg viewBox="0 0 24 24" aria-hidden="true"><path d="M2 5h20v14H2zm2 2v.4l8 5.2 8-5.2V7zm0 2.8V17h16V9.8l-8 5.2z"/></svg>
          info@vitalis-partner.de
        </p>
        <p class="contact__row">
          <svg viewBox="0 0 24 24" aria-hidden="true"><path d="M12 2a10 10 0 1 0 0 20 10 10 0 0 0 0-20zm-1 17.9A8 8 0 0 1 4.1 11H7c.1 3.3 1.6 6.4 4 8.9zM7 9H4.1A8 8 0 0 1 11 4.1C8.6 6.6 7.1 5.7 7 9zm6 10.9c2.4-2.5 3.9-5.6 4-8.9h2.9a8 8 0 0 1-6.9 8.9zM17 9c-.1-3.3-1.6-2.4-4-4.9A8 8 0 0 1 19.9 9zM9 11h6c-.1 2.8-1.2 5.4-3 7.4-1.8-2-2.9-4.6-3-7.4zm0-2c.1-2.8 1.2-5.4 3-7.4 1.8 2 2.9 4.6 3 7.4z"/></svg>
          www.vitalis-partner.de
        </p>
      </div>
    </div>
  </section>
</body>
</html>
```